Brivolt Technologies business card design

We need a business card designed with our new logo. it would be great if the card could communicate it is a technology based company.

Target Market(s)

system integrators

Industry/Entity Type

technology, IOT

Contact Information for Business Card

Name, designation, Address, telephone number, email address

Requirements
Must have
• logo and company name
Nice to have
• something to do with technology

```html
<!DOCTYPE html>
<html lang="en">
<head>
<meta charset="utf-8">
<title>Brivolt Technologies – Business Card</title>
<link href="https://fonts.googleapis.com/css2?family=Montserrat:wght@400;500;700&display=swap" rel="stylesheet">
<style>
  :root {
    --backdrop: #c9c9c9;
    --charcoal: #3e3e40;
    --paper: #ffffff;
    --orange: #f7941d;
    --ink-light: #ffffff;
  }
  * { box-sizing: border-box; margin: 0; padding: 0; }
  html, body {
    width: 1200px; height: 813px; overflow: hidden;
    background: var(--backdrop);
    font-family: "Montserrat", Arial, sans-serif;
  }
  .sheet {
    position: relative; width: 1200px; height: 813px;
    display: flex; align-items: center; justify-content: center; gap: 30px;
  }
  .card {
    position: relative; width: 540px; height: 309px; overflow: hidden;
    box-shadow: 0 10px 24px rgba(0,0,0,0.25);
  }
  .card--front { background: var(--paper); }
  .card--back { background: var(--charcoal); }

  .front-shape { position: absolute; inset: 0; }

  .brand {
    position: absolute; display: flex; align-items: center; gap: 10px;
    font-weight: 700; letter-spacing: 0.04em; line-height: 1;
  }
  .brand__mark { display: block; background: var(--orange); flex: none; }
  .brand__text { display: flex; flex-direction: column; gap: 4px; }
  .brand__name { text-transform: uppercase; }
  .brand__sub { text-transform: uppercase; letter-spacing: 0.3em; }

  .card--front .brand { top: 34px; left: 250px; color: var(--charcoal); z-index: 1; }
  .card--front .brand__mark { width: 26px; height: 26px; }
  .card--front .brand__name { font-size: 30px; }
  .card--front .brand__sub { font-size: 10px; }

  .card--back .brand { top: 50%; left: 50%; transform: translate(-50%, -50%); color: var(--ink-light); gap: 18px; }
  .card--back .brand__mark { width: 48px; height: 48px; }
  .card--back .brand__name { font-size: 54px; }
  .card--back .brand__sub { font-size: 17px; }

  .contact {
    position: absolute; left: 26px; top: 174px; color: var(--ink-light);
  }
  .contact__name {
    color: var(--orange); font-weight: 700; font-size: 15px;
    letter-spacing: 0.03em; text-transform: uppercase;
  }
  .contact__role { font-size: 11.5px; margin-top: 2px; }
  .contact__address { font-size: 11px; font-style: normal; line-height: 1.35; margin-top: 7px; }
  .contact__list { list-style: none; margin-top: 6px; font-size: 11px; line-height: 1.45; }
  .contact__item { display: flex; align-items: center; gap: 8px; }
  .contact__icon { width: 12px; height: 12px; fill: var(--orange); flex: none; }
</style>
</head>
<body>
<main class="sheet">
  <section class="card card--front" aria-label="Card front">
    <svg class="front-shape" viewBox="0 0 540 309" preserveAspectRatio="none" aria-hidden="true">
      <path fill="var(--charcoal)" d="M0,309 V180 C6,156 50,150 170,146 C340,140 480,124 540,58 V309 Z"/>
      <path fill="none" stroke="var(--orange)" stroke-width="4" stroke-linecap="round"
            d="M0,166 C8,140 50,134 170,130 C335,124 470,108 526,24"/>
    </svg>

    <div class="brand">
      <span class="brand__mark"></span>
      <div class="brand__text">
        <span class="brand__name">Brivolt</span>
        <span class="brand__sub">Technologies</span>
      </div>
    </div>

    <div class="contact">
      <p class="contact__name">Daryn Holloway</p>
      <p class="contact__role">Co-Founder</p>
      <address class="contact__address">Corvane Plaza 2810 Mill<br>Brookfield RD Suite 118</address>
      <ul class="contact__list">
        <li class="contact__item">
          <svg class="contact__icon" viewBox="0 0 24 24" aria-hidden="true"><path d="M6.6 10.8a15 15 0 0 0 6.6 6.6l2.2-2.2a1 1 0 0 1 1-.25 11.4 11.4 0 0 0 3.6.57 1 1 0 0 1 1 1V20a1 1 0 0 1-1 1A17 17 0 0 1 3 4a1 1 0 0 1 1-1h3.5a1 1 0 0 1 1 1c0 1.25.2 2.45.57 3.57a1 1 0 0 1-.25 1z"/></svg>
          555-014-2763
        </li>
        <li class="contact__item">
          <svg class="contact__icon" viewBox="0 0 24 24" aria-hidden="true"><path d="M2 5h20v14H2z M3.5 6.5 12 13l8.5-6.5" stroke="var(--charcoal)" stroke-width="1.5"/></svg>
          info@brivolt.com
        </li>
        <li class="contact__item">
          <svg class="contact__icon" viewBox="0 0 24 24" aria-hidden="true"><circle cx="12" cy="12" r="10"/><path d="M2 12h20M12 2c3 3 3 17 0 20M12 2c-3 3-3 17 0 20" fill="none" stroke="var(--charcoal)" stroke-width="1.4"/></svg>
          www.brivolt.com
        </li>
      </ul>
    </div>
  </section>

  <section class="card card--back" aria-label="Card back">
    <div class="brand">
      <span class="brand__mark"></span>
      <div class="brand__text">
        <span class="brand__name">Brivolt</span>
        <span class="brand__sub">Technologies</span>
      </div>
    </div>
  </section>
</main>
</body>
</html>
```